New Business Card Design Project

I need a design for business cards, i am an electrical business called "Corvane Electrical and Communications" i need the cards to be double sided with the company logo on the back (attached) the front needs to say my company name, web site, email address, telephone number, and ABN number and electrical license number. I am open to different arrangements of the information but would like the background to be incorporating something electrical or something that looks smart. open to all additional ideas also.

The company colours are orange and grey see logo attached.

Business Name: Corvane Electrical and Communications
Website: corvaneelectricalandcomms.example.com.au
Email: brent@corvaneelectricalandcomms.example.com.au
Telephone(mobile): 0481209736
ABN: 71208349162
Lic No: 418273D

Target Market(s)

Business entities, Project Managers, Accounts, Clients

Industry/Entity Type

Electrician

Contact Information for Business Card

I need a design for business cards, i am an electrical business called "Corvane Electrical and Communications" i need the cards to be double sided with the company logo on the back (attached) the front needs to say my company name

Font styles to use
Serif
Sans Serif

Colors
f37122
5c5c5c

Requirements
Must have
• Must have the Logo on the back open to different ways of it being on the back but had in mind to keep it central but again open to other options
Nice to have
• A real modern cool background that is eye catching yet contemporary
Should not have
• No backgrounds of a light bulb or plug or anything like that

```html
<!DOCTYPE html>
<html lang="en">
<head>
<meta charset="utf-8">
<title>Corvane Electrical and Communications – Business Card</title>
<link rel="stylesheet" href="https://fonts.googleapis.com/css2?family=Exo+2:wght@400;500;600;700&display=swap">
<style>
  :root {
    --orange: #f37122;
    --orange-deep: #c9550f;
    --grey: #5c5c5c;
    --card-dark: #1f1f1f;
    --card-mid: #3b3b3b;
    --text-light: #ececec;
    --text-dim: #d2d2d2;
    --ink-on-orange: #2a2a2a;
    --page-bg: #e7e5e2;
  }
  * { margin: 0; padding: 0; box-sizing: border-box; }
  html, body {
    width: 1200px;
    height: 969px;
    overflow: hidden;
    background: var(--page-bg);
    font-family: "Exo 2", "Trebuchet MS", sans-serif;
  }
  .canvas {
    position: relative;
    width: 1200px;
    height: 969px;
  }
  .business-card {
    position: absolute;
    left: 100px;
    top: 200px;
    width: 1000px;
    height: 570px;
    border-radius: 30px;
    overflow: hidden;
    background: linear-gradient(160deg, var(--card-mid) 0%, #2a2a2a 45%, var(--card-dark) 100%);
    box-shadow: 0 18px 40px rgba(0, 0, 0, 0.22);
  }
  .contact-block {
    position: absolute;
    left: 44px;
    top: 44px;
    color: var(--text-light);
  }
  .person-name {
    font-size: 36px;
    font-weight: 700;
    color: var(--orange);
    line-height: 1.1;
  }
  .person-role {
    font-size: 27px;
    font-weight: 500;
    margin-top: 4px;
    color: var(--text-light);
  }
  .contact-mobile {
    font-size: 26px;
    margin-top: 24px;
  }
  .contact-mobile .label {
    color: var(--orange);
    font-weight: 600;
  }
  .contact-email {
    font-size: 21px;
    margin-top: 10px;
    color: var(--text-dim);
  }
  .contact-web {
    font-size: 23px;
    margin-top: 10px;
    color: var(--text-dim);
  }
  .brand-name {
    position: absolute;
    right: 50px;
    top: 86px;
    text-align: right;
    color: var(--text-dim);
    font-weight: 600;
    font-size: 30px;
    line-height: 1.2;
    letter-spacing: 1px;
    text-transform: uppercase;
  }
  .energy-band {
    position: absolute;
    left: 0;
    right: 0;
    bottom: 0;
    height: 300px;
    background: linear-gradient(180deg,
      rgba(243, 113, 34, 0) 0%,
      rgba(243, 113, 34, 0.55) 30%,
      var(--orange) 62%,
      var(--orange-deep) 100%);
  }
  .card-footer {
    position: absolute;
    left: 44px;
    right: 44px;
    bottom: 26px;
    display: flex;
    justify-content: space-between;
    font-size: 25px;
    font-weight: 500;
    color: var(--ink-on-orange);
  }
</style>
</head>
<body>
<main class="canvas">
  <section class="business-card">
    <div class="energy-band" role="img" aria-label="Orange electrical wave graphic with a plug across the lower part of the card"></div>

    <div class="contact-block">
      <p class="person-name">Dane Holloway</p>
      <p class="person-role">CEO/Founder</p>
      <p class="contact-mobile"><span class="label">Mobile :</span> 0481209736</p>
      <p class="contact-email">brent@corvaneelectricalandcomms.example.com.au</p>
      <p class="contact-web">corvaneelectricalandcomms.example.com.au</p>
    </div>

    <p class="brand-name">Corvane<br>Electrical &amp; Communications</p>

    <div class="card-footer">
      <span class="abn">ABN: 71208349162</span>
      <span class="licence">Lic No: 418273D</span>
    </div>
  </section>
</main>
</body>
</html>
```